Upstart Retirement Planning Firm needs help with business card design

Harborview Nest Advisors, LLC is looking for help with business card design. We give advice on investments, insurance, and other financial matters related to retirement. There are some required disclosures that we will provide but mostly we are looking for a professional, classy business card that reflects the theme we have chosen. We have a logo that is attached but we would like to add a phrase; "Turning Your Earned Income Into Retirement Income"

Doubled sided only so that we can add the required disclosures (needed for our industry) on the back of the card. We will provide the exact words for this in 1-2 days.

Target Market(s)

Retirees and Pre-retirees. Professionals 50+ years old

Industry/Entity Type

Financial Planning

Contact Information for Business Card

We currently have two people who will need separate cards so we'd like to have a template so that we can add names for new cards in the future.

For the first run, please show the following information.

Gregor Pelham, MBA, ChFC®, CLU®
Financial Advisor, Registered Representative
gpelham@harborviewnest.example
Phone: (555) 318-2946
Toll Free Fax: (800) 555-0193

Address is
2187 Meadowlark Ridge Rd.
Suite K418
Marlow Point, NV 23999

Colors
3277b5

Requirements
Must have
• Logo, contact info, small phase to describe business (in description), required legal disclosures on back of the card as follows (in small font)
• Gregor Pelham is a registered representative of and offers securities through Brightmoor Capital Brokerage Corporation, Member FNQX. Brightmoor Capital Brokerage Corporation is a member of the Brightmoor Capital Alliance which is the marketing name for Brightmoor Holding Corporation and its affiliates.
Nice to have
• Rounded edges, raised letters
Should not have
• any colors that aren't in the logo (other than black for font)

```html
<!DOCTYPE html>
<html lang="en">
<head>
<meta charset="utf-8">
<title>Harborview Nest Advisors – Business Card</title>
<link rel="stylesheet" href="https://fonts.googleapis.com/css2?family=Open+Sans:wght@400;600;700&display=swap">
<style>
  :root {
    --brand-blue: #3277b5;
    --band-gray: #b9bbbe;
    --band-gray-light: #d3d5d7;
    --ink: #2b2b2b;
    --card-white: #fbfbfb;
    --backdrop: #e8e6e2;
  }
  * { margin: 0; padding: 0; box-sizing: border-box; }
  html, body {
    width: 1200px; height: 843px; overflow: hidden;
    background: var(--backdrop);
    font-family: "Open Sans", Arial, sans-serif;
    color: var(--ink);
  }
  .stage { position: relative; width: 1200px; height: 843px; }
  .card {
    position: absolute;
    width: 640px; height: 366px;
    border-radius: 20px;
    background: var(--card-white);
    overflow: hidden;
    box-shadow: 0 6px 18px rgba(0,0,0,.12);
  }
  .card-back { left: 60px; top: 48px; }
  .card-front { left: 500px; top: 428px; }

  /* wordmark */
  .wordmark {
    position: absolute; left: 0; right: 0;
    text-align: center;
    color: var(--brand-blue);
    font-weight: 600;
    font-size: 30px;
    letter-spacing: .5px;
  }
  .card-back .wordmark { top: 92px; }
  .card-front .wordmark { top: 52px; left: 40px; right: 40px; font-size: 28px; }

  /* back */
  .tagline {
    position: absolute; top: 196px; left: 0; right: 0;
    text-align: center; color: var(--brand-blue);
    font-weight: 600; font-size: 19px;
  }
  .disclosure {
    position: absolute; top: 240px; left: 56px; right: 56px;
    text-align: center; font-size: 13px; line-height: 1.45;
  }

  /* front */
  .band { position: absolute; inset: 0; }
  .advisor {
    position: absolute; top: 128px; left: 180px; right: 30px;
    text-align: center;
  }
  .advisor-name {
    color: var(--brand-blue); font-weight: 700; font-size: 22px;
  }
  .advisor-name small { font-size: 15px; font-weight: 600; }
  .advisor-title { font-size: 15px; margin-top: 2px; }
  .contact-list {
    position: absolute; left: 30px; top: 200px;
    list-style: none; font-size: 15px; line-height: 1.75;
  }
  .contact-list li { display: flex; align-items: center; gap: 10px; }
  .contact-list svg { width: 15px; height: 15px; fill: var(--brand-blue); flex: none; }
  .address {
    position: absolute; right: 34px; top: 248px;
    text-align: right; font-size: 16px; line-height: 1.55; font-style: normal;
  }
</style>
</head>
<body>
<main class="stage">

  <section class="card card-back" aria-label="Card back">
    <div class="wordmark">Harborview Nest Advisors, LLC</div>
    <p class="tagline">Turning Your Earned Income Into Retirement Income</p>
    <p class="disclosure">Lorem ipsum dolor sit amet, in nisl persequeris vel, ne quo eligendi sententiantur mediocritatem an. Pro et oratio ubique prodesset. Cum oporteat consetetur seo eo. Sea liber persius te. Te per vero dicat ei.</p>
  </section>

  <section class="card card-front" aria-label="Card front">
    <svg class="band" viewBox="0 0 640 366" aria-hidden="true">
      <defs>
        <linearGradient id="bandShade" x1="0" y1="0" x2="0" y2="1">
          <stop offset="0" stop-color="var(--band-gray-light)"/>
          <stop offset="1" stop-color="var(--band-gray)"/>
        </linearGradient>
      </defs>
      <path d="M0 168 C200 176 440 200 640 214 L640 366 L0 366 Z" fill="url(#bandShade)"/>
      <path d="M0 168 C200 176 440 200 640 214" fill="none" stroke="#fff" stroke-width="2"/>
    </svg>

    <div class="wordmark">Harborview Nest Advisors, LLC</div>

    <div class="advisor">
      <p class="advisor-name">Gregor Pelham, <small>MBA, ChFC®, CLU®</small></p>
      <p class="advisor-title">Financial Advisor, Registered Representative</p>
    </div>

    <ul class="contact-list">
      <li>
        <svg viewBox="0 0 24 24"><path d="M6.6 10.8a15.1 15.1 0 0 0 6.6 6.6l2.2-2.2a1 1 0 0 1 1-.25 11.4 11.4 0 0 0 3.6.57 1 1 0 0 1 1 1V20a1 1 0 0 1-1 1A17 17 0 0 1 3 4a1 1 0 0 1 1-1h3.5a1 1 0 0 1 1 1c0 1.25.2 2.45.57 3.57a1 1 0 0 1-.25 1z"/></svg>
        (555) 318-2946
      </li>
      <li>
        <svg viewBox="0 0 24 24"><path d="M6.6 10.8a15.1 15.1 0 0 0 6.6 6.6l2.2-2.2a1 1 0 0 1 1-.25 11.4 11.4 0 0 0 3.6.57 1 1 0 0 1 1 1V20a1 1 0 0 1-1 1A17 17 0 0 1 3 4a1 1 0 0 1 1-1h3.5a1 1 0 0 1 1 1c0 1.25.2 2.45.57 3.57a1 1 0 0 1-.25 1z"/></svg>
        (800) 555-0193(Toll Free)
      </li>
      <li>
        <svg viewBox="0 0 24 24"><path d="M2 5h20v14H2z M2 5l10 8 10-8" fill="var(--brand-blue)"/><path d="M3 6l9 7 9-7" fill="none" stroke="#fff" stroke-width="1.6"/></svg>
        gpelham@harborviewnest.example
      </li>
    </ul>

    <address class="address">
      2187 Meadowlark Ridge Rd.<br>
      Suite K418<br>
      Marlow Point, NV 23999
    </address>
  </section>

</main>
</body>
</html>
```